New Fresh design for online Rabbit Game

Hi,

we are a french company working on a online rabbits game for kids, and not kids.

Our website is www.zorvelo.fr, but you can look at the US version : www.quintamble.com

We buy our actual design 2 years ago, but we now think it's too boring and washed out...

We need yours talent to make a really more exacting, more colorful, fresh and dynamic design.

In our game, players have to breed and train rabbits and to make them run races. Players run again friends or players.

Players are kids, between 8 and 15 years. But best players are often parents of these kids !

Our ambiance is clearly funny. We really like if color theme or background look like a nice blue sky, and / or beach. Something that make people happy to come, and say "You are here on holly days to have fun !"

I think the best is if we have 2 layouts, one for the Home page, and one for all other page.

For home page, we are really open to any proposition, we just need to keep our features :
- registration (with rabbit preview)
- connection
- game preview (images slide with small text)
- live race preview (as we have actually)

For other pages layout, we need a layout with a standard container (maybe 850 px width?), and our 2 navigation's bar.

We only need psd, no html integration.

Thanks for your help, please ask me for any questions.
Updates

Hi, 

I have just added some information, concerning layout.

Also we have just committed the budget.

Target Market(s)

Mostly kids between 8 and 15 years.

Industry/Entity Type

It Company

Requirements
Must have
• We already have some characters, like Mr Wimble at the home page and our rabbits. We want to keep all of them, so new design have to match with there style (carton).

If you create an account, you will see we have a big nav bar with 6 tabs, and a little top bar. We absolutely need them to keep a easy navigation in website.

We also need some proposition of element style, like h1, h2, h3, hr, inputs, buttons, notification bubble, etc... So we can work to improve all our pages.
Nice to have
• I think the actual website is a little to wide (about 1000px width). Maybe something like 900px - 850px is more elegant ?
In this case, we can arrange pages to deal with it.

It can be cool if major colors are stil blue and green, to match a little with actual colors. But it's no very important.
Should not have
• We don't want too big header picture (for the all pages layout). I mean, players have to focus on the content.

We don't want photo realistic style, our style is cartoon.

We don't want flash. But Js animations are ok.

```html
<!DOCTYPE html>
<html lang="en">
<head>
<meta charset="utf-8">
<title>Quintamble – Home</title>
<link href="https://fonts.googleapis.com/css2?family=Signika:wght@400;600&family=Arimo&display=swap" rel="stylesheet">
<style>
:root{
  --red:#b8000f;
  --red-dark:#8f0009;
  --grass:#8cc63f;
  --grass-dark:#5f9a1d;
  --blue:#3f7fe0;
  --blue-dark:#2f62c0;
  --yellow:#ffe200;
  --orange:#ffb000;
  --panel:#ffffff;
  --green-title:#8cb03a;
  --red-label:#d4151c;
  --grey:#777;
  --sky-top:#3f8a9a;
  --sky-mid:#b9d5cf;
  --sand:#efe2b0;
  --foot-text:#f6b9a8;
}
*{box-sizing:border-box;margin:0;padding:0}
html,body{width:1200px;height:974px;overflow:hidden}
body{position:relative;font-family:"Signika",sans-serif;
  background:linear-gradient(160deg,var(--sky-top) 0%,var(--sky-mid) 40%,#dfe6cf 65%,var(--sand) 100%);}
.abs{position:absolute}
.header{left:0;top:0;width:1200px;height:110px;background:var(--red);border-bottom:6px solid var(--grass)}
.mascot{left:133px;top:6px;width:115px;height:104px;border-radius:40% 40% 20% 20%;background:linear-gradient(#d8d2b8,#a39c80)}
.flowers{height:16px;border-radius:8px;background:linear-gradient(90deg,#fff,#f6f0c8,#fff)}
.brand{left:280px;top:38px;color:var(--yellow);font-size:30px;font-weight:600;letter-spacing:2px}
.nav{left:656px;top:0;display:flex;height:35px}
.nav a{display:block;padding:0 12px;line-height:36px;color:#fff;font-size:14px;font-weight:600;text-decoration:none;letter-spacing:.5px}
.nav a.active{background:linear-gradient(#a8d65a,var(--grass-dark));border-radius:0 0 6px 6px;width:68px;text-align:center}
.account{left:947px;top:0;width:124px;height:35px;background:linear-gradient(#ffd500,#ffb300);border-radius:0 0 8px 8px;font-size:12px;font-weight:600;color:#7a5a00;text-align:center;line-height:40px}
.main{left:135px;top:141px;width:927px;height:677px;background:linear-gradient(var(--yellow),var(--orange));border-radius:4px;box-shadow:0 2px 6px rgba(0,0,0,.2)}
.banner{left:0;top:0;width:927px;height:54px;background:linear-gradient(var(--blue),var(--blue-dark));border-radius:4px 4px 0 0;color:#fff;text-align:center;line-height:56px;font-size:17px;letter-spacing:.5px}
.panel{background:var(--panel);border-radius:3px;box-shadow:0 1px 3px rgba(0,0,0,.15)}
.title{color:var(--green-title);font-size:18px;letter-spacing:.5px}
.label{font-size:11px;color:var(--red-label);letter-spacing:.3px}
.label b{color:var(--grey);font-weight:400}
.field{height:22px;border:1px solid #d6d6d6;border-radius:3px;box-shadow:inset 0 1px 2px rgba(0,0,0,.1)}
.btn{height:20px;line-height:20px;background:linear-gradient(#9ccc45,var(--grass-dark));color:#fff;font-size:11px;font-weight:600;text-align:center;border-radius:2px}
.choice{font-size:11px;color:var(--grey);font-weight:600;display:flex;justify-content:space-between;width:76px;height:18px;align-items:center}
.choice i{width:8px;height:8px;border-radius:50%;background:var(--red-label)}
.sec-title{color:#c8200f;font-size:18px;letter-spacing:.3px}
.tabs{display:flex;font-size:11px;color:var(--grey);letter-spacing:.3px}
.tabs span{padding:0 6px;height:28px;line-height:30px}
.tabs .on{background:#eef2f8;color:var(--blue-dark);border-radius:3px 3px 0 0;padding:0 12px}
.footer{left:0;top:864px;width:1200px;height:110px;background:var(--red);border-bottom:6px solid var(--grass)}
.foot-text{font-size:10px;color:var(--foot-text);letter-spacing:.4px;text-align:left;line-height:19px;white-space:nowrap}
</style>
</head>
<body>
<header class="header abs">
  <div class="mascot abs" role="img" aria-label="Cartoon rabbit mascot"></div>
  <div class="flowers abs" style="left:245px;top:88px;width:120px"></div>
  <div class="flowers abs" style="left:960px;top:88px;width:118px"></div>
  <div class="brand abs">QUINTAMBLE</div>
  <nav class="nav abs"><a class="active">HOME</a><a>NEWS</a><a>FORUM</a><a>RECORDS</a></nav>
  <div class="account abs">Login &nbsp;|&nbsp; Sign Up</div>
</header>

<main class="main abs">
  <div class="banner abs">THE COOLEST RACING AND BREEDING GAME THERE IS</div>

  <section class="panel abs" style="left:18px;top:86px;width:430px;height:173px">
    <div class="title abs" style="left:17px;top:19px">NEW PLAYER</div>
    <div class="label abs" style="left:17px;top:52px"><b>1 -</b> CHOOSE YOUR BUNNY</div>
    <div class="abs" role="img" aria-label="Rabbit preview" style="left:17px;top:80px;width:66px;height:60px;background:linear-gradient(#e6e1cb,#bdb69a);border-radius:30%"></div>
    <div class="abs" style="left:120px;top:89px">
      <div class="choice"><i></i>Original<i></i></div>
      <div class="choice"><i></i>Gray<i></i></div>
      <div class="choice"><i></i>Male<i></i></div>
    </div>
    <div class="abs" style="left:215px;top:17px;width:1px;height:143px;background:#e2e2e2"></div>
    <div class="abs" style="left:228px;top:22px;font-size:9px;color:var(--green-title)">REGISTER IN JUST A COUPLE OF SECOND!</div>
    <div class="label abs" style="left:229px;top:52px"><b>2 -</b> CHOOSE A USERNAME</div>
    <div class="field abs" style="left:229px;top:72px;width:187px"></div>
    <div class="label abs" style="left:229px;top:111px"><b>3 -</b> OK! WE'RE GOOD TO GO!</div>
    <div class="btn abs" style="left:229px;top:132px;width:56px">PLAY</div>
  </section>

  <section class="panel abs" style="left:469px;top:86px;width:439px;height:173px">
    <div class="abs" role="img" aria-label="Mr Wimble, the turtle race coach" style="left:13px;top:20px;width:110px;height:142px;background:linear-gradient(#8fbe3c,#4e7d22);border-radius:45%"></div>
    <div class="title abs" style="left:139px;top:19px">CONNEXION</div>
    <div class="label abs" style="left:139px;top:52px">USERNAME</div>
    <div class="label abs" style="left:274px;top:52px">PASSWORD</div>
    <div class="field abs" style="left:139px;top:70px;width:123px"></div>
    <div class="field abs" style="left:274px;top:70px;width:123px"></div>
    <div class="abs" style="left:406px;top:70px;width:20px;height:21px;background:var(--blue);border-radius:2px;color:#fff;font-size:13px;text-align:center;line-height:21px">?</div>
    <div class="btn abs" style="left:139px;top:107px;width:56px">PLAY</div>
    <div class="abs" style="left:205px;top:110px;font-family:Arimo,sans-serif;font-style:italic;font-size:11px;color:var(--grey)">Forgotten your password?</div>
  </section>

  <div class="abs" style="left:18px;top:291px;width:890px;height:1px;background:#f2c000"></div>

  <h2 class="sec-title abs" style="left:18px;top:314px;font-weight:400">GAME OVERVIEW</h2>
  <h2 class="sec-title abs" style="left:467px;top:314px;font-weight:400">TAKE PART IN RACES WITH OTHER PLAYERS</h2>

  <section class="panel abs" style="left:18px;top:344px;width:430px;height:293px">
    <div class="tabs abs" style="left:42px;top:9px"><span>YOUR PEN</span><span>YOUR ALLOTMENT</span><span class="on">PROFESSIONS</span><span>UNIVERSE</span></div>
    <div class="abs" role="img" aria-label="Cartoon alchemist and blacksmith characters" style="left:9px;top:37px;width:412px;height:210px;background:radial-gradient(#fff,#e4e4e4);border-radius:3px"></div>
    <p class="abs" style="left:13px;top:256px;width:400px;font-family:Arimo,sans-serif;font-size:11.5px;line-height:13px;color:#888">Blacksmith, Alchemist, Gardner or Scientist! Progress in a profession and learn how to make really powerful objects!</p>
  </section>

  <section class="panel abs" style="left:469px;top:344px;width:439px;height:293px">
    <div class="abs" role="img" aria-label="Live race preview with rabbits on the track" style="left:9px;top:10px;width:421px;height:274px;background:linear-gradient(#3a2a14 0%,#262a30 25%,#2e2412 45%,#1f170a 100%);border-radius:4px"></div>
  </section>
</main>

<footer class="footer abs">
  <div class="flowers abs" style="left:150px;top:92px;width:100px"></div>
  <div class="flowers abs" style="left:940px;top:92px;width:70px"></div>
  <div class="abs" role="img" aria-label="Rabbit mascot" style="left:1012px;top:48px;width:70px;height:56px;background:linear-gradient(#e6e1cb,#bdb69a);border-radius:40%"></div>
  <div class="abs" style="left:136px;top:42px;font-size:11px;color:var(--foot-text);letter-spacing:.4px">PARTNERS:</div>
  <div class="abs" aria-label="Partner badge" style="left:210px;top:29px;width:81px;height:28px;background:#2a58a8;border:1px solid #123"></div>
  <div class="foot-text abs" style="left:700px;top:30px">RULES - GENERAL TERMS AND CONDITIONS - CONTACT - QUINTAMBLE.COM 3.0<br>COPYRIGHT © 2012 QUINTAMBLE</div>
</footer>
</body>
</html>
```